PostCard Design Project

I am making a mailing postcard
I am having the mailing printed using 4 color foil on certain parts.
I am looking for a design that maximizes the foil process where certain parts are done in foil to grab the customers attention (example: if there is a car on the postcard the headlights would be done in foil) .
I am targeting some industries, (auto, real estate, medical, beauty) I would like the post card to have examples of postcard ideas for 2 or 3 of these industries.
specs:
the postcard should be atleast 6.5x9 up to 8.5x11, I don't want to restrict the space for the creative as I don't want everything to look like a huge mess. both sides will be used.
the piece is a direct mail piece so it has to meet requirements of https://www.mailvantor.com/business/pdf/quick-reference-guide.pdf
text will be
"business with no limits, meet mailing with no addresses, gain new customers through "Open Porch Route Drop" reach new customers at their home without needing their address. "
I also want some current print specials I am running included.
-double your order FREE (order 500 business cards and get 1000)
-250 100lb gloss stock brochures 99.00
-business packages (cards, envelopes and letterhead) 299
-1000 flyers 140.40
-5000 postcards 179.99
A list of services
banners
booklets
brochures
business cards
calendars
catalogs
CD/DVD packages
envelopes
event tickets
flyers
hangtags
postcards
posters
presentation folders
rack cards
labels
table tents
window cling and decal
"order 24/7 orders@inkwillow.com" must be included
my logo is InkWillow will be supplied later
ive received some great designs. however Im looking for something a little more modern like some zorvel would put out. if the amount of words is too much please feel free to edit. also an idea i had for the list of services i offer is to have it transparent yet readable as the background of the postcard some small some big but covering the entire backgroud. you can then design on top of that with other thing. just an early morning thought
Reason: I have uploaded a sketch of my idea, please take time to look at it for an accurate depiction of what im looking for. feel free to add elements that make it pop off the page
Reason: We are getting close i will be providing feed back today

```html
<!DOCTYPE html>
<html lang="en">
<head>
<meta charset="utf-8">
<title>InkWillow Postcard</title>
<link href="https://fonts.googleapis.com/css2?family=Archivo+Black&family=Arimo:wght@400;700&display=swap" rel="stylesheet">
<style>
  :root {
    --page: #e9e6e1;
    --card: #0c0c0d;
    --card-soft: #1b1c1e;
    --blue: #1fa3e8;
    --lime: #b3d92c;
    --white: #ffffff;
    --grey-word: #4a4b4f;
    --grey-word-2: #5c5d61;
  }
  * { box-sizing: border-box; margin: 0; padding: 0; }
  html, body { width: 1200px; height: 900px; overflow: hidden; }
  body {
    background: var(--page);
    font-family: "Arimo", Arial, sans-serif;
    position: relative;
  }
  .postcard {
    position: absolute;
    width: 570px;
    height: 390px;
    background: linear-gradient(160deg, var(--card-soft) 0%, var(--card) 55%);
    overflow: hidden;
    box-shadow: 0 8px 24px rgba(0,0,0,.25);
  }
  /* ---------- front ---------- */
  .postcard--front { left: 25px; top: 120px; }
  .front__logo {
    position: absolute; right: 24px; top: 22px;
    color: var(--white); font-weight: 700; font-size: 22px;
  }
  .front__visual {
    position: absolute; right: 0; top: 64px;
    width: 300px; height: 216px;
    background: linear-gradient(120deg, #c4121c 0%, #7e0e14 30%, #d9c7bc 55%, #9a9ca2 78%, #2b2c30 100%);
  }
  .front__headline {
    position: absolute; left: 26px; top: 60px;
    font-family: "Archivo Black", "Arial Black", sans-serif;
    color: var(--blue);
    font-size: 29px; line-height: 1.02;
    text-transform: uppercase;
  }
  .front__headline .shine { font-size: 40px; display: block; margin-top: 2px; }
  .specials {
    position: absolute; left: 26px; top: 238px;
    list-style: none; color: var(--white);
    font-size: 10.5px; line-height: 1.45;
    width: 240px;
  }
  .specials li { padding-left: 13px; position: relative; }
  .specials li::before {
    content: ""; position: absolute; left: 0; top: 4px;
    width: 7px; height: 4px;
    border-left: 2px solid var(--white); border-bottom: 2px solid var(--white);
    transform: rotate(-45deg);
  }
  .front__band {
    position: absolute; left: 0; right: 0; bottom: 0; height: 110px;
    background: linear-gradient(180deg, rgba(255,255,255,.06), rgba(255,255,255,0));
  }
  .front__contact {
    position: absolute; right: 30px; bottom: 36px;
    color: var(--blue); font-weight: 700; font-size: 19px; line-height: 1.2;
  }
  /* ---------- back ---------- */
  .postcard--back { left: 610px; top: 390px; }
  .back__strip {
    position: absolute; left: 0; right: 0; top: 100px; height: 46px;
    background: linear-gradient(180deg, #3a3b3f, #1c1d20);
  }
  .services {
    position: absolute; left: 14px; top: 170px; right: 0;
    font-weight: 700; white-space: nowrap; overflow: hidden;
  }
  .services p { font-size: 15px; line-height: 1.15; color: var(--grey-word); }
  .services p:nth-child(odd) { color: var(--grey-word-2); }
  .services .hl-blue { color: var(--blue); }
  .services .hl-lime { color: var(--lime); }
  .stamp-box {
    position: absolute; right: 24px; top: 16px;
    width: 70px; height: 48px; background: var(--white);
    color: #111; font-size: 9px; text-align: center;
    display: flex; align-items: center; justify-content: center; line-height: 1.1;
  }
  .sample {
    position: absolute; width: 90px; height: 90px; border-radius: 50%;
    background: var(--white);
    box-shadow: 0 0 0 3px var(--blue) inset;
    padding: 8px;
  }
  .sample__fill { width: 100%; height: 100%; border-radius: 50%; border: 3px solid var(--lime); }
  .sample--one { left: 360px; top: 30px; }
  .sample--two { left: 466px; top: 76px; }
  .sample--three { left: 256px; top: 70px; }
  .back__logo {
    position: absolute; left: 26px; bottom: 16px;
    color: var(--white); font-weight: 700; font-size: 24px;
  }
  .back__logo .accent { color: var(--white); }
</style>
</head>
<body>
  <section class="postcard postcard--front">
    <div class="front__band"></div>
    <div class="front__logo">InkWillow Logo</div>
    <div class="front__visual" role="img" aria-label="Collage of sample ads: red sports car front, dental ad, and silver jewelry"></div>
    <h1 class="front__headline">Let us<br>help your<br>buissness<span class="shine">Shine !</span></h1>
    <ul class="specials">
      <li>Double your order FREE (order 500 business cards and get 1000)</li>
      <li>250 100lb gloss stock brochures 99.00</li>
      <li>Business packages (cards, envelopes and letterhead) 299</li>
      <li>1000 flyers 140.40</li>
      <li>5000 postcards 179.99</li>
    </ul>
    <div class="front__contact">24 hr/7 Day<br>orders@inkwillow.com</div>
  </section>

  <section class="postcard postcard--back">
    <div class="back__strip"></div>
    <div class="services">
      <p>banners • booklets • brochures • business cards • CD/DVD packages</p>
      <p>brochures • catalogs • <span class="hl-blue">business cards</span> • envelopes • event tickets</p>
      <p>calendars • <span class="hl-lime">CD/DVD packages</span> • <span class="hl-blue">booklets</span> • hangtags • flyers</p>
      <p><span class="hl-lime">banners</span> • <span class="hl-blue">calendars</span> • <span class="hl-lime">brochures</span> • <span class="hl-blue">envelopes</span> • postcards</p>
      <p>catalogs • <span class="hl-lime">event tickets</span> • <span class="hl-blue">flyers</span> • posters • rack cards</p>
      <p>envelopes • <span class="hl-lime">hangtags</span> • <span class="hl-blue">postcards</span> • <span class="hl-lime">presentation folders</span></p>
      <p>event tickets • <span class="hl-lime">posters</span> • <span class="hl-blue">labels</span> • <span class="hl-lime">rack cards</span> • table tents</p>
      <p>hangtags • labels • <span class="hl-lime">table tents</span> • <span class="hl-blue">window cling and decal</span></p>
      <p>postcards • rack cards • labels • window cling and decal • flyers</p>
    </div>
    <div class="stamp-box">Postage<br>Stamp</div>
    <div class="sample sample--one"><div class="sample__fill" role="img" aria-label="Sample presentation folder" style="background:linear-gradient(135deg,#dfeee6,#7fb9a8)"></div></div>
    <div class="sample sample--two"><div class="sample__fill" role="img" aria-label="Sample CD and DVD packages" style="background:linear-gradient(135deg,#f2c230,#2d8fd0,#d23a3a)"></div></div>
    <div class="sample sample--three"><div class="sample__fill" role="img" aria-label="Sample flyer" style="background:linear-gradient(135deg,#f4f4f6,#b84ea0)"></div></div>
    <div class="back__logo">InkWillow Logo</div>
  </section>
</body>
</html>
```